Dietary supplement package design

We need a design for a range of dietary supplements mentioned below. The colors can be derived from the attached company logo and the package is a plastic bottle for medicines use (attached is a sample). All products will have the same package design and color with a permissible slight change to product name and associated picture/artwork (if any). Please avoid using pictures of humans or animals. We expect to see a label with three panels:
1. Left panel containing instructions, warnings and other information.
2. Front panel containing products name and its unique look
3. Right panel containing nutrient/ingredient information table and address.
The label will dual language (Arabic/English) and we have no issue to use special colors, i.e. UV, gold or silver.
Products names are:
1. Ginkgo biloba
2. Slimming formula
3. Fat Absorber
4. Glutathione
5. Royal Jelly
6. Vitamin D
Target Market(s)
Consumers and health care professionals
Industry/Entity Type
Healthcare

```html
<!DOCTYPE html>
<html lang="en">
<head>
<meta charset="utf-8">
<title>Vitalen Ginkgo Biloba – Supplement Label</title>
<link rel="stylesheet" href="https://fonts.googleapis.com/css2?family=Fira+Sans+Condensed:wght@500;600&family=Open+Sans:wght@400;700&display=swap">
<style>
  :root {
    --backdrop: #6a6a6a;
    --label-dark: #15181f;
    --label-edge: #3a3f48;
    --red-light: #ef3a35;
    --red-deep: #b3141b;
    --red-rim: #e5553a;
    --brand-blue: #2aa7e2;
    --gold-light: #ffe23a;
    --gold-deep: #f2b705;
    --ink-dark: #1b1b1b;
    --white: #ffffff;
  }
  * { box-sizing: border-box; margin: 0; padding: 0; }
  html, body {
    width: 1200px; height: 982px; overflow: hidden;
    background: var(--backdrop);
  }
  .canvas {
    position: relative; width: 1200px; height: 982px;
    display: flex; align-items: center; justify-content: center;
  }
  .label {
    position: relative; width: 560px; height: 700px;
    background: linear-gradient(90deg, var(--label-edge) 0%, var(--label-dark) 12%, var(--label-dark) 88%, var(--label-edge) 100%);
    border-radius: 6px;
    overflow: hidden;
  }
  .title-panel {
    position: absolute; left: 34px; right: 34px; top: 0; height: 360px;
    background: linear-gradient(160deg, var(--red-light) 0%, #e3232a 45%, var(--red-deep) 100%);
    border: 2px solid var(--red-rim); border-top: none;
    border-radius: 0 0 14px 14px;
    display: flex; flex-direction: column; align-items: center; justify-content: flex-end;
    padding-bottom: 28px;
  }
  .brand {
    display: flex; align-items: center; gap: 10px; margin-bottom: 10px;
  }
  .brand-mark {
    width: 18px; height: 18px; background: var(--brand-blue);
  }
  .brand-name {
    font-family: "Open Sans", sans-serif; font-weight: 700;
    font-size: 38px; line-height: 1; color: var(--brand-blue);
  }
  .product-name {
    font-family: "Fira Sans Condensed", sans-serif; font-weight: 600;
    font-size: 76px; line-height: 1; color: var(--white);
    letter-spacing: -0.5px;
  }
  .supplement-band {
    position: absolute; left: 34px; right: 34px; top: 384px; height: 50px;
    background: linear-gradient(180deg, var(--gold-light) 0%, var(--gold-deep) 100%);
    border-radius: 3px;
    display: flex; align-items: center; justify-content: center;
    font-family: "Open Sans", sans-serif; font-weight: 700;
    font-size: 28px; letter-spacing: 0.5px; color: var(--ink-dark);
  }
  .formula-note {
    position: absolute; left: 0; right: 0; top: 488px;
    text-align: center;
    font-family: "Open Sans", sans-serif; font-weight: 400;
    font-size: 22px; line-height: 1.35; color: var(--white);
  }
  .count-band {
    position: absolute; left: 0; right: 0; bottom: 0; height: 82px;
    background: linear-gradient(180deg, #d91f26 0%, var(--red-light) 50%, var(--red-deep) 100%);
    display: flex; align-items: center; justify-content: center; gap: 8px;
    font-family: "Open Sans", sans-serif; color: var(--white);
  }
  .count-number { font-size: 34px; font-weight: 700; }
  .count-unit { font-size: 20px; font-weight: 400; }
</style>
</head>
<body>
  <main class="canvas">
    <section class="label" aria-label="Supplement bottle front label">
      <header class="title-panel">
        <div class="brand">
          <span class="brand-mark" aria-hidden="true"></span>
          <span class="brand-name">Vitalen</span>
        </div>
        <h1 class="product-name">Ginkgo Biloba</h1>
      </header>
      <div class="supplement-band">DIETARY SUPPLEMENT</div>
      <p class="formula-note">Formulated with Garcinia Cambogia<br>and Green Tea extracts</p>
      <footer class="count-band">
        <span class="count-number">30</span>
        <span class="count-unit">Tablets</span>
      </footer>
    </section>
  </main>
</body>
</html>
```